Boutique Real Estate Brokerage Tessly Realty Website Design

Winning designer work on migrate as well through nest ferry.
We need a new website as an informational hub to aid our print and digital strategy as well as showing that we are located in Brooklyn and Florida. I have a boutique real estate brokerage and advisory firm specializing in residential leasing, multifamily sales and 1031 Exchange appropriation. This won't be a portal to search properties, it will be a place for information. I'd like space for an ebook to be downloaded and information on my probate sales and multifamily leasing marketing campaigns. I included my logo and will leave it up to the designer to come up with colors to match it. I have also attached verbiage for each page. The final design should have a modern high end look that reflects gentrifying Brooklyn as well as beautiful Florida.
Thank you!
Target Market(s)
Owners of income producing real estate and develop-able land in Brooklyn, NY and Florida.
Industry/Entity Type
Real Estate
Coding
Coded - Design and coding required
Number of Pages Required
5+ page
Colors
Designer to choose colors to be used in the design.
Requirements
Must have
- A modern elegant look
Nice to have
- pictures of brooklyn and florida
Should not have
- real estate search pages

```html
<!DOCTYPE html>
<html lang="en">
<head>
<meta charset="utf-8">
<title>Tessly Realty</title>
<link rel="stylesheet" href="https://fonts.googleapis.com/css2?family=Jura:wght@500;600&family=Montserrat:wght@400;600;700&family=Open+Sans:wght@400;600&display=swap">
<style>
:root{
  --black:#000;
  --ink:#111;
  --white:#fff;
  --grey-bar:#6b6b6b;
  --night:#1d2433;
  --night-deep:#0e1320;
  --muted:#555;
  --text:#222;
  --icon-grey:#8a8a8a;
}
*{margin:0;padding:0;box-sizing:border-box}
html,body{width:1200px;height:3543px;overflow:hidden}
body{position:relative;background:var(--white);font-family:"Open Sans",Arial,sans-serif;color:var(--text)}
.abs{position:absolute}
.heading{font-family:"Jura",Arial,sans-serif;font-weight:600}

/* header */
.site-header{left:0;top:0;width:1200px;height:128px;background:var(--black)}
.brand{display:flex;align-items:center;gap:16px;font-family:"Montserrat",Arial,sans-serif;font-weight:700;color:#cfcfcf;letter-spacing:4px;text-transform:uppercase}
.brand-mark{background:#bdbdbd}
.header-brand{left:108px;top:38px;font-size:19px}
.header-brand .brand-mark{width:56px;height:56px}
.support{left:598px;top:18px;display:flex;align-items:center;gap:14px;color:var(--white);font-family:"Montserrat",Arial,sans-serif}
.support strong{display:block;font-size:17px;font-weight:700}
.support span{font-size:17px}
.search{left:848px;top:22px;width:250px;height:42px;background:var(--white);border-radius:21px;display:flex;align-items:center;padding-left:16px;font-size:14px;color:#888}
.search-btn{position:absolute;right:6px;top:6px;width:30px;height:30px;border-radius:50%;background:#888}

/* hero */
.hero{left:0;top:128px;width:1200px;height:580px;background:linear-gradient(100deg,#3a2a22 0%,#6b3a2a 35%,#5c4a3a 55%,#7a3524 75%,#2c3a22 100%)}
.hero-title{left:90px;top:335px;color:var(--white);font-family:"Jura",Arial,sans-serif;font-weight:600;font-size:31px;line-height:50px}
.dots{left:92px;top:452px;display:flex;gap:9px}
.dots i{width:15px;height:15px;border-radius:50%;background:var(--white);border:2px solid var(--white)}
.dots i:first-child{background:transparent}

.tear{left:0;width:1200px}

/* help */
.section-title{width:1200px;text-align:center;font-size:40px;color:var(--ink);left:0}
.lead{left:140px;width:920px;text-align:center;font-size:14.5px;line-height:33px;color:#333}
.service{width:330px;height:216px;top:928px;background:linear-gradient(160deg,#b7c0c6,#6f7a80)}
.service-label{position:absolute;left:0;bottom:0;width:100%;height:40px;background:var(--grey-bar);color:var(--white);font-family:"Montserrat",Arial,sans-serif;font-weight:600;font-size:16px;text-transform:uppercase;display:flex;align-items:center;justify-content:center}

/* dark bands */
.band{left:0;width:1200px}
.story{top:1232px;height:595px;background:linear-gradient(180deg,var(--night) 0%,#27324a 50%,var(--night-deep) 100%)}
.ebook{top:2398px;height:598px;background:linear-gradient(180deg,#2b3444 0%,#3a4350 45%,#1c2a22 100%)}
.band-title{color:var(--white);font-size:40px}
.band-copy{color:var(--white);font-size:14.5px;line-height:31px;text-align:justify}
.btn{background:var(--white);color:var(--ink);font-family:"Montserrat",Arial,sans-serif;font-weight:700;font-size:15px;height:44px;padding:0 18px;display:flex;align-items:center;gap:8px}
.ring{border-radius:50%;border:10px solid #3d4250;box-shadow:0 0 0 2px #666}

/* blog */
.post{width:328px}
.post-img{height:196px;background:linear-gradient(160deg,#8fb2d2,#6c7a5a)}
.post-date{position:absolute;left:12px;top:172px;width:110px;height:30px;background:var(--grey-bar);color:var(--white);font-size:13px;display:flex;align-items:center;justify-content:center;gap:6px}
.post-title{margin-top:42px;font-family:"Montserrat",Arial,sans-serif;font-weight:700;font-size:16.5px;color:var(--ink)}
.post-text{margin-top:12px;font-size:12.5px;line-height:24px;color:#333}
.post-more{margin-top:10px;font-family:"Montserrat",Arial,sans-serif;font-weight:700;font-size:12px}

/* footer */
.site-footer{left:0;top:2996px;width:1200px;height:547px;background:var(--black);color:var(--white)}
.footer-brand{left:0;width:1200px;top:96px;justify-content:center;font-size:22px}
.footer-brand .brand-mark{width:66px;height:66px}
.contact{width:280px;text-align:center;top:228px;font-size:17px;line-height:30px}
.contact-icon{width:86px;height:86px;border-radius:50%;background:var(--icon-grey);margin:0 auto 22px;display:flex;align-items:center;justify-content:center}
.footer-nav{left:0;width:1200px;top:402px;text-align:center;font-size:15px}
.footer-nav span{margin:0 10px}
.social{left:0;width:1200px;top:440px;display:flex;justify-content:center;gap:8px}
.social i{width:30px;height:30px;border-radius:50%;border:2px solid var(--white)}
.copyright{left:0;width:1200px;top:503px;text-align:center;font-size:14px}
</style>
</head>
<body>

<header class="abs site-header">
  <div class="abs brand header-brand"><span class="brand-mark"></span>Tessly Realty</div>
  <div class="abs support">
    <svg width="44" height="44" viewBox="0 0 44 44" aria-hidden="true"><circle cx="22" cy="22" r="20" fill="none" stroke="#fff" stroke-width="2.5"/><path d="M15 12c2 0 3 4 3 5s-2 2-2 3c1 3 4 6 7 7 1 0 2-2 3-2s5 1 5 3-2 4-4 4c-8 0-15-7-15-15 0-2 1-5 3-5z" fill="#fff"/></svg>
    <div><strong>SUPPORT CALL US</strong><span>555-014-2280</span></div>
  </div>
  <div class="abs search">&#9906; Search<span class="search-btn"></span></div>
</header>

<section class="abs hero" role="img" aria-label="Brooklyn brownstone street with stoops and trees"></section>
<div class="abs hero-title">Assisting landlords increase<br>profits while decreasing the stress.</div>
<div class="abs dots"><i></i><i></i><i></i></div>
<svg class="abs tear" style="top:668px" height="44" viewBox="0 0 1200 44" preserveAspectRatio="none" aria-hidden="true"><path d="M0 20 L40 14 L80 22 L130 10 L190 20 L240 12 L300 24 L360 12 L420 20 L480 8 L540 22 L600 14 L660 24 L720 10 L780 20 L840 12 L900 22 L960 10 L1020 20 L1080 12 L1140 24 L1200 14 L1200 44 L0 44Z" fill="#fff"/></svg>

<h2 class="abs heading section-title" style="top:758px">How we can help</h2>
<p class="abs lead" style="top:826px">Sed ut perspiciatis unde omnis iste natus error sit voluptatem accusantium doloremque laudantium, totam rem aperiam, eaque ipsa quae ab illo inventore veritatis et quasi architecto beatae vitae dicta sunt explicabo.</p>

<div class="abs service" style="left:92px" role="img" aria-label="Bright apartment interior"><div class="service-label">Multi-Family Leasing</div></div>
<div class="abs service" style="left:435px;background:linear-gradient(160deg,#9aa3a0,#6a4a3a)" role="img" aria-label="Brick multifamily building"><div class="service-label">Multi-Family Sales</div></div>
<div class="abs service" style="left:778px;background:linear-gradient(180deg,#a9bfd6,#5f7a56)" role="img" aria-label="Aerial view of Florida land"><div class="service-label">Site Selection Advisory</div></div>

<section class="abs band story" role="img" aria-label="City skyline at dusk"></section>
<svg class="abs tear" style="top:1228px" height="36" viewBox="0 0 1200 36" preserveAspectRatio="none" aria-hidden="true"><path d="M0 0 H1200 V14 L1140 22 L1080 10 L1020 20 L960 8 L900 22 L840 12 L780 24 L720 12 L660 20 L600 8 L540 22 L480 12 L420 24 L360 10 L300 20 L240 12 L180 24 L120 10 L60 22 L0 12Z" fill="#fff"/></svg>
<svg class="abs tear" style="top:1796px" height="36" viewBox="0 0 1200 36" preserveAspectRatio="none" aria-hidden="true"><path d="M0 20 L60 12 L120 24 L180 10 L240 22 L300 14 L360 24 L420 10 L480 20 L540 12 L600 24 L660 12 L720 22 L780 10 L840 20 L900 14 L960 24 L1020 12 L1080 22 L1140 10 L1200 18 V36 H0Z" fill="#fff"/></svg>
<h2 class="abs heading band-title" style="left:90px;top:1382px">Our Story</h2>
<p class="abs band-copy" style="left:92px;top:1446px;width:510px;text-align:left">Tessly Realty NYC•PB is a full-service real estate brokerage firm with offices located in Brooklyn, New York and West Palm Beach, Florida. Our firm focuses on multifamily leasing, sales and Commercial Real Estate Site Selection Advisory.<br>Our clients are private and institutional multifamily real estate investors.</p>
<div class="abs btn" style="left:92px;top:1616px">Read More <span>&#10148;</span></div>
<div class="abs ring" style="left:675px;top:1305px;width:440px;height:440px;background:linear-gradient(160deg,#dfe6ea,#7fa9a0)" role="img" aria-label="Portrait of the firm's founder"></div>

<h2 class="abs heading section-title" style="top:1888px;font-family:Montserrat,Arial,sans-serif;font-weight:700;letter-spacing:1px">OUR BLOG</h2>
<article class="abs post" style="left:90px;top:1960px">
  <div class="post-img" role="img" aria-label="West Palm Beach waterfront towers"></div>
  <div class="post-date">&#9638; Oct 27 2018</div>
  <h3 class="post-title">SED UT PERSPICIATIS UND</h3>
  <p class="post-text">Sed ut perspiciatis unde omnis iste natus error sit voluptatem accusantium doloremque laudantium, totam rem aperiam, eaque ipsa quae ab illo</p>
  <p class="post-more">READ MORE</p>
</article>
<article class="abs post" style="left:435px;top:1960px">
  <div class="post-img" style="background:linear-gradient(160deg,#c9b48a,#5a3a2c)" role="img" aria-label="Brooklyn row house facades"></div>
  <div class="post-date">&#9638; Oct 27 2018</div>
  <h3 class="post-title">SED UT PERSPICIATIS UND</h3>
  <p class="post-text">Sed ut perspiciatis unde omnis iste natus error sit voluptatem accusantium doloremque laudantium, totam rem aperiam, eaque ipsa quae ab illo</p>
  <p class="post-more">READ MORE</p>
</article>
<article class="abs post" style="left:782px;top:1960px">
  <div class="post-img" style="background:linear-gradient(180deg,#9fb6c8,#57704c)" role="img" aria-label="Aerial view of a Florida lake community"></div>
  <div class="post-date">&#9638; Oct 27 2018</div>
  <h3 class="post-title">SED UT PERSPICIATIS UND</h3>
  <p class="post-text">Sed ut perspiciatis unde omnis iste natus error sit voluptatem accusantium doloremque laudantium, totam rem aperiam, eaque ipsa quae ab illo</p>
  <p class="post-more">READ MORE</p>
</article>

<section class="abs band ebook" role="img" aria-label="Florida waterfront city skyline at dusk"></section>
<svg class="abs tear" style="top:2394px" height="36" viewBox="0 0 1200 36" preserveAspectRatio="none" aria-hidden="true"><path d="M0 0 H1200 V16 L1140 8 L1080 22 L1020 12 L960 24 L900 10 L840 22 L780 12 L720 24 L660 10 L600 20 L540 12 L480 24 L420 8 L360 22 L300 12 L240 20 L180 10 L120 24 L60 12 L0 20Z" fill="#fff"/></svg>
<h2 class="abs heading band-title" style="left:90px;top:2545px">EBook</h2>
<p class="abs band-copy" style="left:92px;top:2600px;width:510px">Sed ut perspiciatis unde omnis iste natus error sit voluptatem accusantium doloremque laudantium, totam rem aperiam, eaque ipsa quae ab illo inventore veritatis et quasi architecto beatae vitae dicta sunt explicabo. Nemo enim ipsam voluptatem quia voluptas sit aspernatur aut odit aut fugit, sed quia consequuntur magni dolores eos qui ratione voluptatem sequi nesciunt.</p>
<div class="abs btn" style="left:92px;top:2804px">Read More <span>&#10148;</span></div>
<div class="abs ring" style="left:668px;top:2482px;width:446px;height:446px;background:var(--black);display:flex;align-items:center;justify-content:center">
  <span style="font-family:Montserrat,Arial,sans-serif;font-weight:700;font-size:30px;letter-spacing:4px;color:#cfcfcf">TESSLY</span>
</div>

<footer class="abs site-footer">
  <div class="abs brand footer-brand"><span class="brand-mark"></span>Tessly Realty</div>
  <div class="abs contact" style="left:178px">
    <div class="contact-icon"><svg width="40" height="44" viewBox="0 0 40 44" aria-hidden="true"><path d="M20 3a13 13 0 0 0-13 13c0 10 13 24 13 24s13-14 13-24A13 13 0 0 0 20 3z" fill="none" stroke="#fff" stroke-width="2.5"/><circle cx="20" cy="16" r="5" fill="none" stroke="#fff" stroke-width="2.5"/></svg></div>
    482 Larkin Ave, 3,<br>Brooklyn, New York 11207
  </div>
  <div class="abs contact" style="left:458px">
    <div class="contact-icon"><svg width="40" height="40" viewBox="0 0 40 40" aria-hidden="true"><path d="M10 4c3 0 5 6 5 7s-3 3-3 4c2 5 6 9 11 11 1 0 3-3 4-3s7 2 7 5-3 6-6 6C16 34 6 24 6 12c0-3 2-8 4-8z" fill="none" stroke="#fff" stroke-width="2.5"/></svg></div>
    Phone:<br>555-019-7731
  </div>
  <div class="abs contact" style="left:726px">
    <div class="contact-icon"><svg width="44" height="32" viewBox="0 0 44 32" aria-hidden="true"><rect x="2" y="2" width="40" height="28" fill="none" stroke="#fff" stroke-width="2.5"/><path d="M2 2 L22 18 L42 2" fill="none" stroke="#fff" stroke-width="2.5"/></svg></div>
    Email:<br>marla@tesslyrealty.com
  </div>
  <nav class="abs footer-nav">Home<span>|</span>About Us<span>|</span>Our Services<span>|</span>Signup Now<span>|</span>Contact Us</nav>
  <div class="abs social" aria-label="Social links"><i></i><i></i><i></i><i></i></div>
  <p class="abs copyright">Copyright © 2019. All Right Reserved.</p>
</footer>

</body>
</html>
```